Web design required

1-We need a web design for existing company based in New Zealand
2-We build residential house and light commercial
3-We has in-house designer which allow us can provide interior design
4-We modeling project before site construction, which enable both client and construction team to visually analysis whole project,

Target Market(s)

middle class residential house market
Ref: http://www.parvellbuilders.co.nz/

Industry/Entity Type

Construction Company

Number of Pages Required

1 page

Font styles to use
Sans Serif
Other font styles liked:
• Such as : Central Gothic or similar which has more design taste

Colors

Designer to choose colors to be used in the design.

Requirements
Must have
• Front sheet, contact information, sample project

```html
<!DOCTYPE html>
<html lang="en">
<head>
<meta charset="utf-8">
<title>Harbourline Homes</title>
<link href="https://fonts.googleapis.com/css2?family=Montserrat:wght@500;600;700&family=Questrial&display=swap" rel="stylesheet">
<style>
:root{
  --blue:#0b4ea2;
  --blue-dark:#083f86;
  --grey-panel:#5f5f5f;
  --ink:#2d2d2d;
  --text:#444;
  --light:#e8e8e8;
  --footer:#3c3c3c;
  --footer-base:#323232;
  --rule:#c9c9c9;
  --white:#fff;
}
*{box-sizing:border-box;margin:0;padding:0}
html,body{width:1200px;height:2605px;overflow:hidden}
body{position:relative;background:var(--white);font-family:"Questrial",Arial,sans-serif;color:var(--text)}
.abs{position:absolute}
.heading{font-family:"Montserrat",Arial,sans-serif;font-weight:600;color:var(--ink);font-size:31px;text-align:center;width:1200px;left:0;letter-spacing:.3px}
.heading span{color:var(--blue)}
.ornament{position:absolute;left:385px;width:430px;height:24px}
.btn{position:absolute;background:var(--blue);color:var(--white);font-family:"Montserrat",Arial,sans-serif;font-weight:600;font-size:12px;text-align:center;line-height:30px;height:30px}

/* header */
.topbar{left:735px;top:0;width:330px;height:30px;background:var(--blue);clip-path:polygon(0 0,100% 0,96% 100%,4% 100%);color:var(--white);font-size:12px;display:flex;align-items:center;justify-content:center;gap:18px;white-space:nowrap}
.topbar svg{vertical-align:-2px;margin-right:5px}
.logo{left:142px;top:26px;display:flex;align-items:center;gap:12px}
.logo-square{width:46px;height:46px;background:var(--blue)}
.logo-name{font-family:"Montserrat",Arial,sans-serif;font-weight:600;font-size:22px;color:var(--blue);line-height:1.05}
.nav a{position:absolute;top:58px;font-family:"Montserrat",Arial,sans-serif;font-weight:500;font-size:12.5px;color:var(--ink);text-decoration:none}
.nav .active{color:var(--blue)}
.nav-hex{left:510px;top:40px;width:56px;height:52px}

/* hero */
.hero{left:0;top:104px;width:1200px;height:480px;background:linear-gradient(180deg,#2f7fd3 0%,#4e90d8 45%,#2c4f7a 75%,#1c2a3a 100%)}
.hero-caption{left:0;top:538px;width:1200px;text-align:center;font-family:"Montserrat",Arial,sans-serif;font-weight:500;font-size:26px;color:var(--white)}
.hero-arrow{width:38px;height:38px;border-radius:50%;background:rgba(255,255,255,.35);top:299px}

/* about */
.about-text{left:156px;top:718px;width:890px;text-align:center;font-size:13px;line-height:22px;color:#555}

/* services */
.service{top:919px;width:600px;height:549px}
.service.commercial{left:0;background:var(--blue)}
.service.residential{left:600px;background:var(--grey-panel)}
.service h2{position:absolute;top:57px;font-family:"Montserrat",Arial,sans-serif;font-weight:600;font-size:26px;color:var(--white)}
.service .line{position:absolute;top:97px;height:24px;width:427px}
.service .photo{position:absolute;top:147px;width:427px;height:206px;border:4px solid var(--white)}
.service p{position:absolute;top:373px;width:430px;font-size:12px;letter-spacing:-.1px;line-height:22px;color:var(--white)}

/* projects */
.project{top:1615px;width:222px;height:146px;background:var(--white);box-shadow:0 0 0 1px #e4e4e4;padding:4px}
.project div{width:100%;height:100%}
.project-label{left:4px;top:84px;width:214px;text-align:center;color:var(--white);font-size:14px}
.chev{width:16px;height:26px}

/* testimonials */
.testimonials{left:0;top:1824px;width:1200px;height:472px;background:var(--light)}
.quote{top:1975px;width:296px;height:113px;background:var(--blue);color:var(--white);font-size:12.5px;line-height:22px;padding:22px 14px}
.quote::after{content:"";position:absolute;left:86px;bottom:-18px;border-left:0 solid transparent;border-right:18px solid transparent;border-top:18px solid var(--blue)}
.avatar{top:2109px;width:66px;height:66px;border-radius:50%;border:3px solid var(--white);box-shadow:0 0 0 1px #bbb;background:linear-gradient(#c9c3bb,#8c8a88)}
.client-name{top:2122px;font-family:"Montserrat",Arial,sans-serif;font-weight:600;color:var(--blue);font-size:15px}
.client-role{top:2146px;font-size:13px;color:#333}
.skyline{left:142px;top:2204px;width:918px;height:92px;background:linear-gradient(0deg,#4a4a4a,#6a6a6a);clip-path:polygon(0 60%,8% 60%,8% 45%,25% 45%,25% 35%,40% 35%,42% 20%,52% 20%,52% 50%,62% 50%,62% 40%,72% 40%,72% 25%,80% 25%,80% 0,84% 0,84% 30%,92% 30%,92% 15%,100% 15%,100% 100%,0 100%)}

/* footer */
.footer{left:0;top:2296px;width:1200px;height:261px;background:var(--footer)}
.footer-base{left:0;top:2557px;width:1200px;height:48px;background:var(--footer-base);border-top:1px solid #4a4a4a;color:#ddd;font-size:12px;text-align:center;line-height:48px}
.f-title{top:2337px;font-family:"Montserrat",Arial,sans-serif;font-weight:600;font-size:13px;color:var(--white)}
.f-title::after{content:"";position:absolute;left:0;top:22px;width:34px;height:2px;background:#777}
.f-sep{top:2335px;width:1px;height:190px;background:#555}
.links li{list-style:none;position:absolute;left:0;font-size:12px;color:#eee;white-space:nowrap}
.links li::before{content:"»";color:#999;margin-right:10px}
.contact{color:#eee;font-size:12px;line-height:17px}
.contact svg{position:absolute;left:0;top:1px}
.contact div{position:absolute;left:22px;white-space:nowrap}
.field{left:636px;width:189px;background:var(--white);color:#999;font-size:11px;font-style:italic;padding:6px 8px}
.submit{left:636px;top:2494px;width:72px;height:25px;background:var(--blue);color:var(--white);font-family:"Montserrat",Arial,sans-serif;font-weight:600;font-size:12px;text-align:center;line-height:25px}
.brand-foot{left:900px;top:2356px;width:200px;text-align:center;font-family:"Montserrat",Arial,sans-serif;font-weight:600;font-size:19px;color:#cfcfcf}
.brand-mark{left:975px;top:2392px;width:50px;height:50px;background:#9a9a9a}
.social{top:2472px;width:24px;height:24px;border-radius:50%;background:#8a8a8a}
</style>
</head>
<body>

<!-- header -->
<div class="abs topbar">
  <span><svg width="12" height="12" viewBox="0 0 24 24" fill="#fff"><path d="M6.6 10.8a15.1 15.1 0 0 0 6.6 6.6l2.2-2.2c.3-.3.7-.4 1-.2 1.1.4 2.3.6 3.6.6.6 0 1 .4 1 1V20c0 .6-.4 1-1 1A17 17 0 0 1 3 4c0-.6.4-1 1-1h3.5c.6 0 1 .4 1 1 0 1.3.2 2.5.6 3.6.1.3 0 .7-.2 1z"/></svg>123 456 7890</span>
  <span><svg width="12" height="10" viewBox="0 0 24 18" fill="#fff"><path d="M0 0h24v2L12 10 0 2zM0 4l12 8 12-8v14H0z"/></svg>hello@harbourlinehomes.co.nz</span>
</div>
<div class="abs logo">
  <div class="logo-square"></div>
  <div class="logo-name">HARBOURLINE<br>HOMES</div>
</div>
<svg class="abs nav-hex" viewBox="0 0 56 52"><polygon points="14,2 42,2 55,26 42,50 14,50 1,26" fill="#eef0f3"/></svg>
<nav class="nav">
  <a class="active" style="left:523px">HOME</a>
  <a style="left:606px">ABOUT US</a>
  <a style="left:714px">SERVICES</a>
  <a style="left:816px">RECENT PROJECTS</a>
  <a style="left:976px">CONTACT US</a>
</nav>

<!-- hero -->
<div class="abs hero" role="img" aria-label="Glass office towers against a blue evening sky"></div>
<div class="abs hero-arrow" style="left:85px"><svg width="38" height="38" viewBox="0 0 38 38"><path d="M22 11l-8 8 8 8" stroke="#fff" stroke-width="3" fill="none"/></svg></div>
<div class="abs hero-arrow" style="left:1077px"><svg width="38" height="38" viewBox="0 0 38 38"><path d="M16 11l8 8-8 8" stroke="#fff" stroke-width="3" fill="none"/></svg></div>
<div class="abs hero-caption">We Build Residential House And Light Commercial</div>

<!-- about -->
<h1 class="abs heading" style="top:639px">ABOUT <span>HARBOURLINE HOMES</span></h1>
<svg class="ornament" style="top:685px" viewBox="0 0 430 24"><line x1="0" y1="12" x2="196" y2="12" stroke="#c9c9c9" stroke-dasharray="2 3"/><line x1="234" y1="12" x2="430" y2="12" stroke="#c9c9c9" stroke-dasharray="2 3"/><polygon points="215,1 225,6.5 225,17.5 215,23 205,17.5 205,6.5" fill="#c4c4c4"/></svg>
<p class="abs about-text">Lorem ipsum dolor sit amet, consectetuer adipiscing elit, sed diam nonummy nibh euismod tincidunt ut laoreet dolore magna aliquam erat volutpat. Ut wisi enim ad minim veniam, quis nostrud exerci tation ullamcorper suscipit lobortis nisl ut aliquip ex ea commodo consequat. Duis autem vel eum iriure dolor in hendrerit in vulputate velit esse molestie consequat, vel illum dolore eu feugiat nulla facilisis at vero eros et accumsan et iusto odio dignissim qui blandit praesent luptatum zzril delenit augue duis dolore te feugait nulla facilisi nibh euismod tincidunt ut laoreet dolore magna.</p>
<div class="btn" style="left:551px;top:825px;width:99px">READ MORE</div>

<!-- services -->
<section class="abs service commercial">
  <h2 style="left:143px">COMMERCIAL SERVICES</h2>
  <svg class="line" style="left:143px" viewBox="0 0 427 24"><polygon points="10,1 20,6.5 20,17.5 10,23 0,17.5 0,6.5" fill="#8fb0da"/><line x1="32" y1="12" x2="427" y2="12" stroke="#8fb0da" stroke-dasharray="2 3"/></svg>
  <div class="photo" style="left:143px;background:linear-gradient(180deg,#5d7fa8,#a89a93 60%,#6b6f78)" role="img" aria-label="Curved multi-storey commercial building at dusk"></div>
  <p style="left:145px">Lorem ipsum dolor sit amet, consectetuer adipiscing elit, sed diam nonummy nibh euismod tincidunt ut laoreet dolore magna aliquam erat volutpat. Ut wisi enimad minim veniam, quis nostrud exerci tation ullamcorper.</p>
  <div class="btn" style="left:143px;top:455px;width:98px;background:var(--grey-panel)">READ MORE</div>
</section>
<section class="abs service residential">
  <h2 style="left:31px">RESIDENTIAL SERVICES</h2>
  <svg class="line" style="left:31px" viewBox="0 0 427 24"><polygon points="10,1 20,6.5 20,17.5 10,23 0,17.5 0,6.5" fill="#9a9a9a"/><line x1="32" y1="12" x2="427" y2="12" stroke="#8a8a8a" stroke-dasharray="2 3"/></svg>
  <div class="photo" style="left:31px;background:linear-gradient(180deg,#2f6fd0,#8fb0d8 45%,#c9c6be 65%,#6f8a55)" role="img" aria-label="Two-storey family house with a garage under blue sky"></div>
  <p style="left:31px">Lorem ipsum dolor sit amet, consectetuer adipiscing elit, sed diam nonummy nibh euismod tincidunt ut laoreet dolore magna aliquam erat volutpat. Ut wisi enimad minim veniam, quis nostrud exerci tation ullamcorper.</p>
  <div class="btn" style="left:28px;top:455px;width:98px">READ MORE</div>
</section>

<!-- recent projects -->
<h2 class="abs heading" style="top:1523px">RECENT <span>PROJECTS</span></h2>
<svg class="ornament" style="top:1569px" viewBox="0 0 430 24"><line x1="0" y1="12" x2="196" y2="12" stroke="#c9c9c9" stroke-dasharray="2 3"/><line x1="234" y1="12" x2="430" y2="12" stroke="#c9c9c9" stroke-dasharray="2 3"/><polygon points="215,1 225,6.5 225,17.5 215,23 205,17.5 205,6.5" fill="#c4c4c4"/></svg>
<svg class="abs chev" style="left:102px;top:1674px" viewBox="0 0 16 26"><path d="M13 2L3 13l10 11" stroke="#999" stroke-width="2" fill="none"/></svg>
<div class="abs project" style="left:142px"><div style="background:linear-gradient(180deg,#3d7fd6,#6b8fb5 55%,#4a5560)" role="img" aria-label="Modern glass office building"></div></div>
<div class="abs project" style="left:373px"><div style="background:linear-gradient(180deg,#4c86d8,#c8cbd0 55%,#5f7d45)" role="img" aria-label="White two-storey suburban house"></div></div>
<div class="abs project" style="left:606px"><div style="background:linear-gradient(180deg,#2a3550,#4c5b70 60%,#6e7766)" role="img" aria-label="Dark clad commercial building"></div>
  <svg class="abs" style="left:97px;top:38px" width="28" height="28" viewBox="0 0 28 28"><circle cx="14" cy="14" r="12" stroke="#fff" stroke-width="1.5" fill="none"/><path d="M14 8v12M8 14h12" stroke="#fff" stroke-width="1.5"/></svg>
  <div class="abs project-label">Laoreet Dolore Magna</div></div>
<div class="abs project" style="left:838px"><div style="background:linear-gradient(180deg,#3a74c9,#b8a88f 55%,#6b8a4e)" role="img" aria-label="Row of suburban homes"></div></div>
<svg class="abs chev" style="left:1081px;top:1674px" viewBox="0 0 16 26"><path d="M3 2l10 11L3 24" stroke="#999" stroke-width="2" fill="none"/></svg>

<!-- testimonials -->
<section class="abs testimonials"></section>
<h2 class="abs heading" style="top:1878px">CLIENT <span>TESTIMONIALS</span></h2>
<svg class="ornament" style="top:1925px" viewBox="0 0 430 24"><line x1="0" y1="12" x2="196" y2="12" stroke="#c4c4c4" stroke-dasharray="2 3"/><line x1="234" y1="12" x2="430" y2="12" stroke="#c4c4c4" stroke-dasharray="2 3"/><polygon points="215,1 225,6.5 225,17.5 215,23 205,17.5 205,6.5" fill="#bdbdbd"/></svg>
<svg class="abs chev" style="left:102px;top:2016px" viewBox="0 0 16 26"><path d="M13 2L3 13l10 11" stroke="#999" stroke-width="2" fill="none"/></svg>
<svg class="abs chev" style="left:1081px;top:2016px" viewBox="0 0 16 26"><path d="M3 2l10 11L3 24" stroke="#999" stroke-width="2" fill="none"/></svg>

<div class="abs quote" style="left:142px">Lorem ipsum dolor sit amet, consectetuer adipig elit, sed diam nonummy nibh euismod tincidunt ut laoreet dolore magna aliquam volutpat.</div>
<div class="abs avatar" style="left:153px" role="img" aria-label="Client portrait"></div>
<div class="abs client-name" style="left:233px">LOREM IPSUM</div>
<div class="abs client-role" style="left:233px">Lorem ipsum dolor sit amet</div>

<div class="abs quote" style="left:452px">Lorem ipsum dolor sit amet, consectetuer adipig elit, sed diam nonummy nibh euismod tincidunt ut laoreet dolore magna aliquam volutpat.</div>
<div class="abs avatar" style="left:464px" role="img" aria-label="Client portrait"></div>
<div class="abs client-name" style="left:544px">LOREM IPSUM</div>
<div class="abs client-role" style="left:544px">Lorem ipsum dolor sit amet</div>

<div class="abs quote" style="left:763px">Lorem ipsum dolor sit amet, consectetuer adipig elit, sed diam nonummy nibh euismod tincidunt ut laoreet dolore magna aliquam volutpat.</div>
<div class="abs avatar" style="left:775px" role="img" aria-label="Client portrait"></div>
<div class="abs client-name" style="left:855px">LOREM IPSUM</div>
<div class="abs client-role" style="left:855px">Lorem ipsum dolor sit amet</div>

<div class="abs skyline" role="img" aria-label="Silhouettes of construction vehicles, workers, cranes and buildings"></div>

<!-- footer -->
<footer class="abs footer"></footer>
<div class="abs f-title" style="left:143px">QUICK LINKS</div>
<ul class="abs links" style="left:145px;top:2377px">
  <li style="top:0">Home</li>
  <li style="top:23px">About Us</li>
  <li style="top:47px">Services</li>
  <li style="top:71px">Recent Projects</li>
  <li style="top:94px">Contact Us</li>
</ul>
<div class="abs f-sep" style="left:306px"></div>

<div class="abs f-title" style="left:366px">CONTACT DETAILS</div>
<div class="abs contact" style="left:366px;top:2377px">
  <svg width="12" height="14" viewBox="0 0 12 16" fill="#eee"><path d="M6 0a6 6 0 0 1 6 6c0 4-6 10-6 10S0 10 0 6a6 6 0 0 1 6-6zm0 3.5a2.5 2.5 0 1 0 0 5 2.5 2.5 0 0 0 0-5z"/></svg>
  <div style="top:0">HARBOURLINE HOMES</div>
  <div style="top:17px">0907 Lorem ipsum amet</div>
  <div style="top:34px">co adipiscitsededml.</div>
</div>
<div class="abs contact" style="left:366px;top:2438px">
  <svg width="12" height="12" viewBox="0 0 24 24" fill="#eee"><path d="M6.6 10.8a15.1 15.1 0 0 0 6.6 6.6l2.2-2.2c.3-.3.7-.4 1-.2 1.1.4 2.3.6 3.6.6.6 0 1 .4 1 1V20c0 .6-.4 1-1 1A17 17 0 0 1 3 4c0-.6.4-1 1-1h3.5c.6 0 1 .4 1 1 0 1.3.2 2.5.6 3.6.1.3 0 .7-.2 1z"/></svg>
  <div style="top:0">123.456.7890</div>
</div>
<div class="abs contact" style="left:366px;top:2465px">
  <svg width="13" height="12" viewBox="0 0 26 24" fill="#eee"><path d="M6 0h14v6H6zM0 8h26v10h-4v6H4v-6H0zm7 6v7h12v-7z"/></svg>
  <div style="top:0">123.456.7890</div>
</div>
<div class="abs contact" style="left:366px;top:2497px">
  <svg width="14" height="12" viewBox="0 0 24 20" fill="none" stroke="#eee" stroke-width="2"><path d="M2 8l10-6 10 6v10H2zM2 8l10 6 10-6"/></svg>
  <div style="top:0">hello@harbourlinehomes.co.nz</div>
</div>
<div class="abs f-sep" style="left:575px"></div>

<div class="abs f-title" style="left:636px">QUICK INQUIRY</div>
<div class="abs field" style="top:2380px;height:26px">Name</div>
<div class="abs field" style="top:2411px;height:25px">Email</div>
<div class="abs field" style="top:2442px;height:42px">Message</div>
<div class="abs submit">SUBMIT</div>
<div class="abs f-sep" style="left:882px"></div>

<div class="abs brand-foot">HARBOURLINE</div>
<div class="abs brand-mark"></div>
<div class="abs social" style="left:955px"></div>
<div class="abs social" style="left:982px"></div>
<div class="abs social" style="left:1009px"></div>
<div class="abs social" style="left:1036px"></div>

<div class="abs footer-base">Copyright © 2017 HARBOURLINE HOMES. All Rights Reserved.</div>

</body>
</html>
```